Report-Design  für Social-Media-Beratungs-Agentur
Report-Design für Social-Media-Beratungs-Agentur
Zielgruppe
Wir sind eine Social-Media-Beratungs-Agentur, die KMU bei der strategischen Ausrichtung und Umsetzung ihrer Social-Media-Präsenzen berät und unterstützt.
Aufgabenstellung
Wir analysieren die Vernetra Profile von Unternehmen in einer Excel-Datei, indem wir in einem Reiter verschiedene Aspekte bewerten. Aus diesen Bewertungen ergibt sich dann in einem zweiten Reiter ein Report (hängt hier an), in den die Ergebnisse aus der 1. Mappe automatisch übernommen werden. Dieser Report wird als PDF gespeichert und an den Kunden geschickt. Wir möchten das Report-Design gerne neu gestalten lassen: Es soll zeitgemäß, professionell und kompetent wirken und nicht mehr 'wie in Excel zusammengebastelt'. Ein Beispiel für ein Design, das uns gefällt, hängt als Inspiration an. Gerne können Grafikelemente aus Canva oder anderen Grafikprogrammen eingefügt werden. Wichtig ist, dass die Struktur mit den Zellen, in die Daten automatisch übernommen werden (im Anhang durch # gekennzeichnet), erhalten bleibt. Unsere Firmenfarben sind: #f69f25, #11323a, #809398, #fcfefd. Wir haben noch weitere Analysen, die wir bei Erfolg dieses Auftrags ebenfalls gerne optimieren lassen möchten.

```html
<!DOCTYPE html>
<html lang="en">
<head>
<meta charset="utf-8">
<title>Social Media Presence Analysis</title>
<link href="https://fonts.googleapis.com/css2?family=Inter:wght@400;500;600&display=swap" rel="stylesheet">
<style>
  :root {
    --bg: #c7e5de;
    --paper: #fcfefd;
    --ink: #11323a;
    --ink-soft: #2f4a51;
    --muted: #809398;
    --rule: #d3d9da;
    --mint: #c6e5dd;
    --teal: #6aafa7;
    --accent: #f69f25;
    --photo-a: #8d9396;
    --photo-b: #dde1e1;
  }
  * { margin: 0; padding: 0; box-sizing: border-box; }
  html, body { width: 1200px; height: 900px; overflow: hidden; }
  body { background: var(--bg); font-family: "Inter", Arial, sans-serif; color: var(--ink); position: relative; }

  .report {
    position: absolute; left: 94px; top: 91px;
    width: 1013px; height: 712px;
    background: var(--paper); border-radius: 10px; overflow: hidden;
  }
  .report > * { position: absolute; }

  .agency { left: 38px; top: 30px; font-size: 13.5px; color: var(--ink-soft); }
  .title { left: 40px; top: 103px; font-size: 61px; font-weight: 600; line-height: 68px; letter-spacing: -1.8px; white-space: nowrap; }

  .rule { background: var(--rule); }
  .rule-h { height: 1px; }
  .rule-v { width: 1px; }

  .highlights-title { left: 754px; top: 150px; font-size: 22px; font-weight: 500; line-height: 26px; }
  .highlights-text { left: 754px; top: 195px; width: 222px; font-size: 13px; line-height: 17.7px; color: var(--ink-soft); }

  .data-code { left: 41px; top: 515px; font-size: 22px; line-height: 26px; }

  .dot {
    border-radius: 50%; display: flex; align-items: center; justify-content: center;
    font-size: 33px; font-weight: 600;
  }
  .dot-accent { left: 239px; top: 344px; width: 110px; height: 110px; background: var(--accent); }
  .dot-mint { left: 364px; top: 344px; width: 110px; height: 110px; background: var(--mint); }
  .dot-teal { left: 21px; top: 563px; width: 106px; height: 106px; background: var(--teal); }
  .dot-corner { left: 914px; top: 584px; width: 130px; height: 130px; background: var(--mint); justify-content: flex-start; padding-left: 27px; }

  .item-title { font-size: 16.5px; font-weight: 500; line-height: 20px; }
  .item-text { font-size: 12.5px; line-height: 16px; color: var(--ink-soft); margin-top: 8px; }
  .next-steps { left: 266px; top: 504px; }
  .profile-analysis { left: 266px; top: 603px; }

  .photo {
    left: 542px; top: 345px; width: 331px; height: 367px;
    border-radius: 166px 166px 0 0;
    background: linear-gradient(160deg, var(--photo-b), var(--photo-a));
  }
  .ring { left: 888px; top: 501px; width: 88px; height: 88px; border-radius: 50%; border: 11px solid var(--mint); }
  .dome { left: 754px; top: -31px; width: 215px; height: 215px; border-radius: 50%; background: var(--mint); clip-path: inset(0 0 50% 0); }
</style>
</head>
<body>
  <main class="report">
    <div class="dome"></div>
    <p class="agency">Marketing Agency</p>
    <h1 class="title">Social Media<br>Presence Analysis</h1>

    <div class="rule rule-v" style="left:707px;top:0;height:482px"></div>
    <div class="rule rule-h" style="left:42px;top:316px;width:432px"></div>
    <div class="rule rule-v" style="left:220px;top:316px;height:396px"></div>
    <div class="rule rule-h" style="left:0;top:481px;width:1013px"></div>
    <div class="rule rule-h" style="left:220px;top:570px;width:322px"></div>

    <h2 class="highlights-title">Highlights</h2>
    <p class="highlights-text">Lorem ipsum performance tool with key insights on social channels and audience growth across every platform to support strong and effective engagement and analytics.</p>

    <svg class="chart-mark" style="left:0;top:0" width="222" height="712" viewBox="0 0 222 712" aria-hidden="true">
      <path d="M0 459 L0 430 C15 370 80 336 185 334 A13 13 0 0 1 185 360 C120 362 75 392 52 459 Z" fill="var(--mint)"/>
      <rect x="0" y="459" width="208" height="200" fill="var(--mint)"/>
      <g fill="var(--mint)">
        <rect x="86" y="415" width="10" height="45"/>
        <rect x="106" y="399" width="10" height="61"/>
        <rect x="125" y="420" width="10" height="40"/>
        <rect x="144" y="403" width="10" height="57"/>
        <rect x="177" y="430" width="10" height="30"/>
        <rect x="196" y="448" width="10" height="12"/>
      </g>
      <path d="M141 466 Q162 418 220 407" fill="none" stroke="var(--rule)" stroke-width="1"/>
    </svg>

    <p class="data-code">#8909238</p>
    <div class="dot dot-teal">#</div>
    <div class="dot dot-accent">#</div>
    <div class="dot dot-mint">#</div>

    <div class="next-steps">
      <h3 class="item-title">Next Steps</h3>
      <p class="item-text">an overview of the next actions</p>
    </div>
    <div class="profile-analysis">
      <h3 class="item-title">Vernetra Analysis</h3>
      <p class="item-text">and an overview of the profile</p>
    </div>

    <div class="photo" role="img" aria-label="Photo of three colleagues in business attire gathered around a laptop"></div>
    <div class="rule rule-v" style="left:932px;top:481px;height:104px"></div>
    <div class="ring"></div>
    <div class="dot dot-corner">#</div>
  </main>
</body>
</html>
```